Start-Up für Training, Coaching & Consulting sucht modernes Webdesign!
Zielgruppe
Wer ist TAVI Training, Coaching & Consulting?
Wir führen Führungskräftetrainings durch, machen Privatkunden für Bewerbungen fit und unterstützen Unternehmen mit Verkaufstrainings. Wir entwickeln Persönlichkeiten im Coaching. Wir beraten Unternehmen und helfen ihnen dabei, ihre Geschäftsabläufe und Prozesse zu optimieren. Dabei steht unsere hohe Qualität im Mittelpunkt - gemeinsam mit unseren kreativen Trainingsmethoden. Unser Background (Diplom-Kaufleute und geprüfte Trainer) bietet dafür die passende Ausgangslage.
Was bedeutet TAVI?
Tavi ist Maori und bdeutet Kreis/Spirale. Er symbolisiert einen wachsenden Silberfarn und steht für persönliche Entwicklung und Entfaltung. Der Tavi ist einerseits unser Namensgeber und unser Logo, andererseits steht der Tavi aber auch für unsere Werte: Denn wir wollen unseren Kunden dabei helfen zu wachsen und sich weiterzuentwickeln - und dies auf eine hochqualitative und seriöse Art und Weise ohne den Eindruck von Esoterik oder Erlebnispädagogik zu vermitteln.
Aufgabenstellung
Modernes Design, das unsere Philosophie widerspiegelt: Wir möchten unseren Kunden auf seriöse und hochqualitative Weise weiterentwickeln. Wir stehen für nachhaltigen Lernerfolg, kreative Trainingsmethoden, Abwechslung, Spaß am Lernen, Qualität, Kompetenz, Fachwissen und Dynamik.
Layout:
1) Header: QMSR geprüfter Trainer, Menüpunkte (siehe Architektur)
2) Banner
3) 3 Teaser (Training, Coaching, Consulting) + Header + 2-3 Zeilen Text (+Icons)
>>> Sichtbarer Bereich auf Homepage: Menü, Banner, Teaser
4) "Warum Sie uns wählen sollten": 5 bullet points ohne weiteren Text
5) "Aus unserem Blog": Frame für 3 Blogartikel + Bild + Datum + Header + 2-3 Zeilen Text
6) Alle drei QMSR Logos
7) Footer: Click Us (quick links), Contact Us (Adresse), Follow Us (Pinnwald, ZOLP, Kontaktor)
8) Copyright + Impressum
>>> Das Design soll klar sein, aber nicht zu kantig. Vielmehr sollen abgerundete Ecken und dynamische Elemente genutzt werden.
Architektur:
3 Ebenen:
1) Homepage
2) TAVI, Training, Coaching, Consulting, für Trainer, Kundenstimmen/Referenzen, Kontakt
3) noch zu bestimmende Produktdetailseiten
Texte werden noch erstellt, Layout kann ggf. mit Platzhaltertext gefüllt werden.
Bildmaterial: Logo und vorhandenes Imagebild werden zur Verfügung gestellt. Bilder können ggf. gekauft werden. Vorschläge erwünscht.
Corporate colors:
grün: #a2c61b + monochromatic colors
http://www.tintoskop.de/a2c61b
grau: #474747 + monochromatic colors
http://www.tintoskop.de/474747

```html
<!DOCTYPE html>
<html lang="de">
<head>
<meta charset="utf-8">
<title>TAVI Training, Coaching &amp; Consulting</title>
<link href="https://fonts.googleapis.com/css2?family=Nunito+Sans:wght@300;400;600;700;800&display=swap" rel="stylesheet">
<style>
:root{
  --lime:#a2c61b;
  --lime-light:#cfe36a;
  --lime-pale:#eef5d2;
  --ink:#2f3133;
  --grey:#474747;
  --footer:#2b2e31;
  --footer-text:#b9bcbf;
  --white:#ffffff;
  --forest-dark:#1f4a10;
  --forest:#3f7d1c;
  --forest-light:#7fb338;
}
*{margin:0;padding:0;box-sizing:border-box}
html,body{width:795px;height:1200px;overflow:hidden;background:var(--white)}
body{font-family:"Nunito Sans",sans-serif;color:var(--ink);position:relative}
.abs{position:absolute}
/* hero */
.hero{left:0;top:0;width:795px;height:335px}
.site-header{left:0;top:0;width:795px;height:53px;background:rgba(40,48,38,.72)}
.brand{left:112px;top:9px;color:var(--white)}
.brand-name{font-weight:800;font-size:22px;letter-spacing:1px;line-height:24px}
.brand-tag{font-size:5px;color:var(--lime-light);letter-spacing:.2px}
.cert-badge{left:201px;top:19px;width:66px;height:18px;background:#1f6db4;border-radius:2px}
.nav{left:302px;top:0;height:53px;display:flex;align-items:center;font-size:9px;color:var(--white);letter-spacing:.2px}
.nav .item{padding:0 9px;line-height:53px;display:flex;align-items:center;gap:3px}
.nav .active{background:#26292a;color:var(--lime);border-bottom:2px solid var(--lime);line-height:51px}
.nav .sep{opacity:.9;padding:0 3px}
.nav .chev{color:var(--lime);font-size:7px}
.hero-title{left:0;width:795px;top:118px;text-align:center;color:var(--white);font-weight:300;font-size:30px;line-height:35px;letter-spacing:.3px}
.hero-title b{font-weight:800}
.hero-sub{left:0;width:795px;top:188px;text-align:center;color:var(--white);font-size:13px;font-weight:400}
.btn-hero{left:347px;top:215px;width:99px;height:33px;border-radius:17px;background:var(--lime);color:var(--white);font-weight:700;font-size:8px;display:flex;align-items:center;justify-content:center;letter-spacing:.2px}
/* teasers */
.teaser{top:368px;width:168px}
.teaser-icon{left:0;top:0;width:42px;height:42px;border-radius:50%;background:var(--lime);border:2px solid var(--white)}
.teaser-title{left:0;width:100%;top:4px;text-align:center;color:var(--lime);font-weight:600;font-size:12px;padding-left:20px}
.teaser-img{left:20px;top:22px;width:161px;height:105px;border-radius:14px}
.teaser-text{left:20px;width:161px;top:141px;text-align:center;font-size:7px;line-height:10px;color:var(--ink);border-top:1px dotted #777;padding-top:4px;margin:0}
/* dividers */
.divider-line{height:1px;background:#d6d6c8}
.divider-dot{width:22px;height:22px;border-radius:50%;background:var(--lime-pale);border:3px solid var(--lime-light)}
/* why */
.section-title{font-size:17px;font-weight:400;color:var(--ink);padding-bottom:8px;border-bottom:1px dotted #777}
.why-list{left:118px;top:664px;list-style:none}
.why-list li{display:flex;align-items:center;gap:8px;height:29.6px;font-size:12.5px;color:var(--ink)}
.why-list .tick{width:15px;height:15px;border-radius:50%;background:var(--lime);color:var(--white);font-size:8px;display:flex;align-items:center;justify-content:center;font-weight:800}
/* blog */
.post{left:467px;width:210px}
.post-img{left:0;top:0;width:60px;height:38px;border-radius:6px}
.post-date{left:68px;top:0;font-size:7px;color:var(--lime);white-space:nowrap}
.post-text{left:68px;top:10px;width:142px;font-size:7px;line-height:10.5px;color:var(--ink)}
.post-more{left:65px;width:38px;height:12px;border-radius:6px;background:var(--lime);color:var(--white);font-size:6.5px;text-align:center;line-height:12px}
.post-sep{left:0;width:197px;border-top:1px dotted #a9b56a}
/* footer */
.footer-brand{left:117px;top:1006px;color:var(--white)}
.footer-brand .brand-name{font-size:16px;line-height:18px}
.footer-brand .brand-tag{font-size:3.5px;color:var(--footer-text)}
.quick-links{left:117px;top:1044px;list-style:none;font-size:8px;color:var(--footer-text);line-height:16px}
.contact-head{font-size:8.5px;color:var(--lime)}
.contact-lines{font-size:6.5px;line-height:12.5px;color:var(--footer-text);margin-top:5px}
.follow-head{left:604px;top:1046px;font-size:8.5px;color:var(--footer-text);letter-spacing:.3px}
.social{top:1062px;width:22px;height:22px;border-radius:50%;background:var(--lime);color:var(--white);font-size:8px;font-weight:700;display:flex;align-items:center;justify-content:center}
.footer-rule{left:117px;top:1135px;width:560px;border-top:1px dotted #6e7a3a}
.copyright{left:0;width:795px;top:1140px;text-align:center;font-size:8.5px;line-height:12.5px;color:var(--footer-text)}
.copyright .title{color:var(--lime)}
</style>
</head>
<body>

<!-- hero -->
<svg class="abs hero" viewBox="0 0 795 335" role="img" aria-label="Hero image: unfurling green fern fronds, softly blurred">
  <defs>
    <radialGradient id="heroBg" cx="50%" cy="40%" r="70%">
      <stop offset="0" stop-color="#5f9a2a"/>
      <stop offset=".6" stop-color="#3f7d1c"/>
      <stop offset="1" stop-color="#1f4a10"/>
    </radialGradient>
    <linearGradient id="limeBand" x1="0" x2="1">
      <stop offset="0" stop-color="#e4f08a"/>
      <stop offset="1" stop-color="#a2c61b"/>
    </linearGradient>
  </defs>
  <rect width="795" height="335" fill="url(#heroBg)"/>
  <path d="M0 268 C150 255 250 300 400 318 C560 336 700 300 795 208 L795 335 L0 335 Z" fill="url(#limeBand)"/>
  <path d="M0 290 C150 268 260 310 400 324 C560 340 700 310 795 232 L795 335 L0 335 Z" fill="#ffffff"/>
  <polyline points="70,150 50,169 70,188" fill="none" stroke="#ffffff" stroke-opacity=".75" stroke-width="8" stroke-linecap="round"/>
  <polyline points="725,150 745,169 725,188" fill="none" stroke="#ffffff" stroke-opacity=".75" stroke-width="8" stroke-linecap="round"/>
</svg>

<header class="abs site-header">
  <div class="abs brand">
    <div class="brand-name">TAVI</div>
    <div class="brand-tag">Training • Coaching • Consulting</div>
  </div>
  <div class="abs cert-badge" role="img" aria-label="Certified trainer badge"></div>
  <nav class="abs nav">
    <span class="item active">HOME</span><span class="sep">I</span>
    <span class="item">ÜBER UNS <span class="chev">▼</span></span><span class="sep">I</span>
    <span class="item">FÜR TRAINERS <span class="chev">▼</span></span><span class="sep">I</span>
    <span class="item">REFERENZEN</span><span class="sep">I</span>
    <span class="item">KONTAKT</span>
  </nav>
</header>

<h1 class="abs hero-title">TRAINING, COACHING<br>CONSULTING <b>FÜR TRAINER</b></h1>
<p class="abs hero-sub">Lorem ipsum dolor sit amet consectetur adipiscing elit.</p>
<div class="abs btn-hero">MEHR ERFAHREN</div>

<!-- teasers -->
<section class="abs teaser" style="left:109px">
  <div class="abs teaser-icon"></div>
  <div class="abs teaser-title">COACHING</div>
  <div class="abs teaser-img" role="img" aria-label="Photo: clasped hands of a businessman over a notebook" style="background:linear-gradient(160deg,#9cc0ea,#5d84c2 60%,#dfe6ee)"></div>
  <p class="abs teaser-text">Lorem ipsum dolor sit amet, consectetur adipiscing elit. In dapibus accumsan luctus.</p>
</section>
<section class="abs teaser" style="left:295px">
  <div class="abs teaser-icon"></div>
  <div class="abs teaser-title">CONSULTING</div>
  <div class="abs teaser-img" role="img" aria-label="Photo: two colleagues reviewing a tablet in an office" style="background:linear-gradient(150deg,#e8ecef,#c9cfd4 50%,#3a3f48)"></div>
  <p class="abs teaser-text">Dolor sit amet, consectetur adipiscing elit. In dapibus accumsan luctus.</p>
</section>
<section class="abs teaser" style="left:481px">
  <div class="abs teaser-icon"></div>
  <div class="abs teaser-title">TRAINING</div>
  <div class="abs teaser-img" role="img" aria-label="Photo: team meeting around a table with tablet and documents" style="background:linear-gradient(160deg,#dfe3e6,#b9a8a0 55%,#e9e2dd)"></div>
  <p class="abs teaser-text">Sit amet, consectetur adipiscing elit. In dapibus accumsan luctus.</p>
</section>

<!-- divider -->
<div class="abs divider-line" style="left:80px;top:584px;width:291px"></div>
<div class="abs divider-line" style="left:424px;top:584px;width:291px"></div>
<div class="abs divider-dot" style="left:386px;top:568px"></div>

<!-- decorative swoosh behind list -->
<svg class="abs" style="left:0;top:770px" width="400" height="90" viewBox="0 0 400 90" aria-hidden="true">
  <path d="M0 58 C120 80 300 90 397 5 L397 30 C330 90 150 90 0 62 Z" fill="#f2f7e0"/>
</svg>

<!-- why -->
<h2 class="abs section-title" style="left:139px;top:620px">WHY CHOOSE US</h2>
<ul class="abs why-list">
  <li><span class="tick">›</span>Vestibulum nec mauris facilisis</li>
  <li><span class="tick">›</span>Curabitur et tristique diam, nec sagittis nibh</li>
  <li><span class="tick">›</span>Denim nec sagittis nibh</li>
  <li><span class="tick">›</span>Vestibulum nec mauris facilisis</li>
  <li><span class="tick">›</span>Tristique diam nec lorem</li>
</ul>

<!-- blog -->
<h2 class="abs section-title" style="left:469px;top:620px">BLOG</h2>

<article class="abs post" style="top:662px">
  <div class="abs post-img" role="img" aria-label="Blog photo: colleagues with a tablet" style="background:linear-gradient(150deg,#e6eaee,#3a3f48)"></div>
  <div class="abs post-date">08.12.2015 Sit Amet Adipiscing</div>
  <p class="abs post-text">Lorem ipsum dolor sit amet, consectetur adipiscing elit. In dapibus accumsan luctus. Aliquam posuere eros sed nibh sagittis,</p>
  <div class="abs post-more" style="top:43px">more</div>
  <div class="abs post-sep" style="top:62px"></div>
</article>
<article class="abs post" style="top:733px">
  <div class="abs post-img" role="img" aria-label="Blog photo: meeting table with documents" style="background:linear-gradient(160deg,#dfe3e6,#b9a8a0)"></div>
  <div class="abs post-date">08.12.2015 Lorem Ipsum Dolor</div>
  <p class="abs post-text">Pellentesque habitant morbi tristique senectus et netus et malesuada fames ac turpis egestas.</p>
  <div class="abs post-more" style="top:44px">more</div>
  <div class="abs post-sep" style="top:62px"></div>
</article>
<article class="abs post" style="top:803px">
  <div class="abs post-img" role="img" aria-label="Blog photo: hands resting on a notebook" style="background:linear-gradient(160deg,#9cc0ea,#5d84c2)"></div>
  <div class="abs post-date">08.12.2015 Adipiscing Vehicula</div>
  <p class="abs post-text">Mauris sollicitudin felis aliquam ipsum dictum vehicula. Donec feugiat sapien nunc, quis auctor libero finibus in.</p>
  <div class="abs post-more" style="top:43px">more</div>
</article>

<!-- divider 2 -->
<div class="abs divider-line" style="left:80px;top:885px;width:291px"></div>
<div class="abs divider-line" style="left:424px;top:885px;width:291px"></div>
<div class="abs divider-dot" style="left:386px;top:869px"></div>

<!-- footer wave + dark footer -->
<svg class="abs" style="left:0;top:890px" width="795" height="310" viewBox="0 0 795 310" aria-hidden="true">
  <defs>
    <linearGradient id="footBand" x1="0" x2="1">
      <stop offset="0" stop-color="#c4dc4a"/>
      <stop offset="1" stop-color="#a2c61b"/>
    </linearGradient>
  </defs>
  <path d="M0 60 C150 40 260 110 420 120 C600 130 720 60 795 0 L795 310 L0 310 Z" fill="url(#footBand)"/>
  <path d="M0 82 C150 70 280 122 420 127 C600 133 720 80 795 30 L795 310 L0 310 Z" fill="var(--footer)"/>
  <path d="M0 0 L795 0 L795 0 C720 60 600 112 420 104 C260 96 150 40 0 52 Z" fill="#ffffff"/>
</svg>

<!-- certificate badges -->
<div class="abs" role="img" aria-label="Certified trainer badge" style="left:273px;top:937px;width:67px;height:19px;background:#1f6db4;border-radius:2px"></div>
<div class="abs" role="img" aria-label="Association member badge" style="left:368px;top:929px;width:54px;height:30px;background:#1f6db4;border-radius:2px"></div>
<div class="abs" role="img" aria-label="Professional association badge" style="left:448px;top:929px;width:71px;height:30px;background:#1f6db4;border-radius:2px"></div>

<!-- footer content -->
<div class="abs footer-brand">
  <div class="brand-name">TAVI</div>
  <div class="brand-tag">Training • Coaching • Consulting</div>
</div>
<ul class="abs quick-links">
  <li>HOME</li><li>ÜBER UNS</li><li>FÜR TRAINERS</li><li>REFERENZEN</li><li>KONTAKT</li>
</ul>

<svg class="abs" style="left:204px;top:1043px" width="14" height="12" viewBox="0 0 14 12" aria-hidden="true"><path d="M7 0 L14 6 L12 6 L12 12 L8.5 12 L8.5 8 L5.5 8 L5.5 12 L2 12 L2 6 L0 6 Z" fill="var(--lime)"/></svg>
<div class="abs" style="left:230px;top:1046px">
  <div class="contact-head">Address</div>
  <div class="contact-lines">Vestibulum nec mauris 62<br>Suscipit est et<br>62134 Townname</div>
</div>

<svg class="abs" style="left:335px;top:1043px" width="12" height="12" viewBox="0 0 12 12" aria-hidden="true"><rect width="12" height="12" rx="2.5" fill="var(--lime)"/><path d="M3.5 2.5 L5 2.5 L5.6 4.4 L4.7 5.2 C5.2 6.3 5.8 6.9 6.8 7.4 L7.6 6.5 L9.5 7.1 L9.5 8.6 C6 8.8 3.3 6 3.5 2.5 Z" fill="var(--footer)"/></svg>
<div class="abs" style="left:361px;top:1046px">
  <div class="contact-head">Phone</div>
  <div class="contact-lines">(000 &nbsp;123 &nbsp;7658 903<br>(000 &nbsp;123 &nbsp;7658 903<br>(000 &nbsp;123 &nbsp;7658 903</div>
</div>

<svg class="abs" style="left:455px;top:1045px" width="13" height="9" viewBox="0 0 13 9" aria-hidden="true"><rect width="13" height="9" rx="1" fill="var(--lime)"/><path d="M0.5 0.8 L6.5 5 L12.5 0.8" fill="none" stroke="var(--footer)" stroke-width="1"/></svg>
<div class="abs" style="left:481px;top:1046px">
  <div class="contact-head">Email</div>
  <div class="contact-lines">info@tavi.com<br>addressinfo@tavi.com<br>emailadd@tavi.com</div>
</div>

<div class="abs follow-head">BITTE FOLGEN</div>
<div class="abs social" style="left:597px" aria-label="Pinnwald">P</div>
<div class="abs social" style="left:625px" aria-label="Zwitscha">Z</div>
<div class="abs social" style="left:653px" aria-label="Kontaktor">K</div>

<div class="abs footer-rule"></div>
<footer class="abs copyright">
  <div class="title">Copyright + Impressum</div>
  <div>Aliquam at pulvinar mi. Nulla eget bibendum nisl. Integer consectetur quam ac purus pharetra pulvinar.</div>
  <div>Aenean faucibus tortor ac tortor aliquet tincidunt. Mauris eget maximus urna.</div>
</footer>

</body>
</html>
```